KRWB new business card design

We need a business card design for our established business which is Australia wide however based in Melbourne. We are a young team of Financial Planners who specialize in Insurance and Basic super advice for people like us.

We are people who help our clients get things done in a timely and cost effective manner whilst having a good time and a laugh along the way.

We would like this to have a consistent feel with our new e-brochure which i have attached from a color and font perspective.

Industry/Entity Type

Business

Requirements
Must have
• We do not need specific address details rather just the states we are in:

VIC/NSW/QLD/TAS
Nice to have
• Curved edge to mate the brochure

```html
<!DOCTYPE html>
<html lang="en">
<head>
<meta charset="utf-8">
<title>KRWB business card set</title>
<link rel="stylesheet" href="https://fonts.googleapis.com/css2?family=Arimo:ital,wght@0,400;0,700;1,700&family=Jost:ital,wght@0,400;0,500;1,600&display=swap">
<style>
  :root {
    --backdrop: #b58a5e;
    --ink-dark: #2b2b2b;
    --ink-grey: #6f6f6f;
    --card-black: #0c0c0c;
    --card-charcoal: #2a2a2a;
    --white: #ffffff;
    --green-light: #6cc04a;
    --green-deep: #00a651;
    --green-faint: #eef4ea;
    --label: #2a1d12;
  }
  * { box-sizing: border-box; margin: 0; padding: 0; }
  html, body { width: 1200px; height: 788px; overflow: hidden; }
  body {
    position: relative;
    background: var(--backdrop);
    font-family: "Arimo", Arial, sans-serif;
  }
  .view-label {
    position: absolute;
    width: 525px;
    text-align: center;
    font-size: 21px;
    color: var(--label);
  }
  .card {
    position: absolute;
    width: 525px;
    height: 300px;
    border-radius: 18px;
    overflow: hidden;
    box-shadow: 0 4px 10px rgba(0,0,0,.35);
  }
  .card--front { left: 53px; top: 72px; background: radial-gradient(circle at 35% 45%, #3a3a3a 0%, var(--card-black) 70%); }
  .card--back-light { left: 622px; top: 74px; background: var(--white); }
  .card--back-plain { left: 53px; top: 445px; background: var(--white); }
  .card--back-dark { left: 622px; top: 446px; background: radial-gradient(circle at 30% 40%, #3a3a3a 0%, var(--card-charcoal) 45%, #111 100%); }

  .swoosh { position: absolute; inset: 0; }

  .brand { position: absolute; text-align: center; }
  .brand__mark { display: block; margin: 0 auto; background: var(--green-light); border-radius: 10px; }
  .brand__name { display: block; font-weight: 700; letter-spacing: 1px; }

  .divider { position: absolute; width: 2px; }
  .card--front .divider { left: 259px; top: 75px; height: 150px; background: linear-gradient(#000, #555 50%, #000); }
  .card--back-light .divider { left: 260px; top: 20px; height: 236px; background: linear-gradient(#fff, #888 50%, #fff); }

  .contact { position: absolute; left: 289px; top: 44px; color: var(--white); }
  .contact__name { font-size: 18px; font-weight: 700; }
  .contact__role { font-size: 13px; font-weight: 700; line-height: 17px; margin-top: 3px; }
  .contact__lines { margin-top: 34px; font-family: "Jost", sans-serif; font-size: 14.5px; line-height: 26px; }
  .contact__lines b { font-style: italic; font-weight: 600; }

  .services { position: absolute; font-weight: 700; }
  .services__title { font-size: 18px; font-style: italic; margin-bottom: 12px; }
  .services__item { font-size: 14px; line-height: 34px; }
  .services__item::before { content: "▪ "; }

  .card--back-light .services { left: 320px; top: 46px; color: var(--ink-grey); }
  .band { position: absolute; left: 0; right: 0; bottom: 0; height: 38px; background: var(--green-light); color: var(--white); font-weight: 700; font-size: 14px; text-align: center; line-height: 38px; }

  .faint-block { position: absolute; left: 150px; top: 14px; width: 226px; height: 272px; background: var(--green-faint); border-radius: 24px; }
  .card--back-plain .services { left: 0; right: 0; top: 46px; text-align: center; color: var(--ink-dark); }
  .tagline-plain { position: absolute; left: 0; right: 0; top: 268px; text-align: center; font-weight: 700; font-size: 14px; color: var(--ink-dark); }

  .card--back-dark .services { left: 313px; top: 24px; color: var(--white); }
  .tagline-green { position: absolute; left: 313px; top: 252px; color: var(--green-light); font-weight: 700; font-size: 14px; line-height: 18px; }
</style>
</head>
<body>
  <div class="view-label" style="left:53px;top:34px;">Front</div>
  <div class="view-label" style="left:622px;top:34px;">Back - 1</div>
  <div class="view-label" style="left:53px;top:404px;">Back - 2</div>
  <div class="view-label" style="left:622px;top:404px;">Back - 3</div>

  <section class="card card--front">
    <svg class="swoosh" width="525" height="300" viewBox="0 0 525 300">
      <path d="M420 0 Q500 10 525 45 L525 30 Q505 5 455 0 Z" fill="var(--green-deep)"/>
      <path d="M440 0 Q505 15 525 60 L525 40 Q505 5 470 0 Z" fill="var(--green-light)"/>
      <path d="M0 250 Q40 290 120 300 L80 300 Q25 290 0 270 Z" fill="var(--green-deep)"/>
      <path d="M0 265 Q50 295 105 300 L60 300 Q20 292 0 282 Z" fill="var(--green-light)"/>
    </svg>
    <div class="brand" style="left:70px;top:55px;width:150px;">
      <span class="brand__mark" style="width:110px;height:110px;"></span>
      <span class="brand__name" style="color:var(--white);font-size:40px;margin-top:40px;">KRWB</span>
    </div>
    <div class="divider"></div>
    <div class="contact">
      <div class="contact__name">Daniel Marsh</div>
      <div class="contact__role">ADFS, BBus, LRS©<br>Financial Adviser</div>
      <div class="contact__lines">
        <div><b>cell</b> 0400 555 218</div>
        <div><b>phone</b> 1300 555 740</div>
        <div><b>fax</b> 03 9555 0182</div>
        <div><b>email</b> daniel@krwb.com.au</div>
        <div><b>web</b> www.krwb.com.au</div>
        <div>VIC/NSW/QLD/TAS</div>
      </div>
    </div>
  </section>

  <section class="card card--back-light">
    <div class="brand" style="left:65px;top:55px;width:150px;">
      <span class="brand__mark" style="width:110px;height:110px;"></span>
      <span class="brand__name" style="color:var(--ink-dark);font-size:30px;margin-top:30px;">KRWB</span>
    </div>
    <div class="divider"></div>
    <div class="services">
      <div class="services__title">Specialising in</div>
      <div class="services__item">Risk Insurance</div>
      <div class="services__item">Debt Management</div>
      <div class="services__item">Superannuation</div>
      <div class="services__item">Wealth Creation</div>
      <div class="services__item">Retirement Planning</div>
    </div>
    <div class="band">SECURE FUTURE, ENHANCED LIFESTYLE</div>
  </section>

  <section class="card card--back-plain">
    <div class="faint-block"></div>
    <div class="services">
      <div class="services__title">Specialising in</div>
      <div class="services__item">Risk Insurance</div>
      <div class="services__item">Debt Management</div>
      <div class="services__item">Superannuation</div>
      <div class="services__item">Wealth Creation</div>
      <div class="services__item">Retirement Planning</div>
    </div>
    <div class="tagline-plain">SECURE FUTURE, ENHANCED LIFESTYLE</div>
  </section>

  <section class="card card--back-dark">
    <div class="brand" style="left:55px;top:25px;width:200px;">
      <span class="brand__mark" style="width:170px;height:170px;"></span>
      <span class="brand__name" style="color:var(--white);font-size:48px;margin-top:28px;">KRWB</span>
    </div>
    <div class="services">
      <div class="services__title">Specialising in</div>
      <div class="services__item">Risk Insurance</div>
      <div class="services__item">Debt Management</div>
      <div class="services__item">Superannuation</div>
      <div class="services__item">Wealth Creation</div>
      <div class="services__item">Retirement Planning</div>
    </div>
    <div class="tagline-green">SECURE FUTURE<br>ENHANCED LIFESTYLE</div>
  </section>
</body>
</html>
```